Packaging design - Biodegradable straws

Hi, my product is "natural 100% biodegradable straws" made from sugarcane and agave fibers. I am looking for packaging (200 units in the box) which would be eye catchy in grocery stores and online stores. Please work with the box template in the attachments (brown cardboard box, not white)

Please check website www.pelvarix.com, facebook and instragram for more info.

i just posted on november 21st and it shows that only 1 day left for project.. need extension

Target Market(s)

Grocery stores and internet sales, female targeted market

Industry/Entity Type

Grocery Store

Colors
00a990
33b8a4
ffffff
cfeae6

Requirements
Must have
• Eye catchy
Original
Clean ("not too busy")
Small company's logo (Pelvarix) incorporated
Other logos (see attachments - KMB approved, ) included somewhere
Statement "not made in China"
Statement "100% biodegradable"
Colours - black, green or white
Nice to have
• it could have an abstract turtle shape somewhere

The following statements can be included:
• Compostable
• Vegan, gluten-free
• Plastic free, Non-toxic
• Biodegrades in less than 24 months
• Made from renewable resources
• Eco friendly and low environmental impact
• Does not get soggy or leave any residue in the drink
• Not made in China
Should not have
• No pandas, no bamboos, straws do not bend

```html
<!DOCTYPE html>
<html lang="en">
<head>
<meta charset="utf-8">
<title>Pelvarix Biodegradable Straws – Box Panels</title>
<link href="https://fonts.googleapis.com/css2?family=Comfortaa:wght@400;700&family=Kalam:wght@300;400&family=Pragati+Narrow:wght@400;700&display=swap" rel="stylesheet">
<style>
  :root {
    --teal: #36b8a4;
    --teal-deep: #00a990;
    --teal-shade: #33aa96;
    --mint: #cfeae6;
    --kraft: #c79d6e;
    --kraft-dark: #b98c5e;
    --ink: #1c1a17;
    --white: #ffffff;
    --page: #f3f2ef;
    --band-h: 185px;
  }
  * { box-sizing: border-box; margin: 0; padding: 0; }
  html, body { width: 1200px; height: 1200px; overflow: hidden; }
  body {
    background: var(--page);
    position: relative;
    font-family: "Kalam", cursive;
  }
  .box-net {
    position: absolute;
    top: 160px; left: 90px;
    width: 1020px; height: 880px;
    display: flex;
    box-shadow: 0 18px 40px rgba(0,0,0,0.12);
  }
  .panel {
    position: relative;
    height: 100%;
    background: var(--kraft);
    overflow: hidden;
  }
  .panel + .panel { border-left: 1px solid var(--kraft-dark); }
  .panel--side { width: 300px; }
  .panel--front { width: 420px; }
  .band {
    position: absolute; top: 0; left: 0; right: 0;
    height: var(--band-h);
    background: var(--teal);
  }
  .panel--side .band { background: var(--teal-shade); }

  /* brand name */
  .brand {
    position: absolute; left: 0; right: 0; top: 122px;
    text-align: center; color: var(--white);
  }
  .brand__name {
    display: inline-flex; align-items: center; gap: 6px;
    font-family: "Pragati Narrow", sans-serif;
    font-size: 24px; font-weight: 400; letter-spacing: 1px;
  }
  .brand__dot {
    width: 9px; height: 9px; border-radius: 50%; background: var(--white);
  }
  .brand__tagline {
    font-family: "Pragati Narrow", sans-serif;
    font-size: 7px; letter-spacing: 1.6px; margin-top: 2px;
  }

  /* front */
  .tear-window { position: absolute; inset: 0; }
  .title {
    position: absolute; left: 0; right: 0; top: 245px;
    text-align: center; color: var(--white);
    font-family: "Comfortaa", sans-serif;
  }
  .title__lead { font-size: 33px; font-weight: 400; letter-spacing: -0.5px; }
  .title__main { font-size: 52px; font-weight: 700; line-height: 1.1; }
  .turtle-art {
    position: absolute; top: 390px; left: 90px;
    width: 240px; height: 340px;
    background: radial-gradient(ellipse at 50% 50%, var(--teal) 0%, var(--teal) 55%, rgba(54,184,164,0.85) 75%, rgba(54,184,164,0) 100%);
    border-radius: 46% 46% 44% 44%;
  }
  .count {
    position: absolute; left: 0; right: 0; top: 790px;
    text-align: center; color: var(--white);
    font-family: "Comfortaa", sans-serif; font-size: 24px;
  }

  /* features side */
  .features {
    position: absolute; top: 270px; left: 26px; right: 18px;
    list-style: none; color: var(--ink);
    font-family: "Kalam", cursive; font-weight: 300;
    font-size: 19px; line-height: 1.3;
  }
  .features li { position: relative; padding-left: 12px; margin-bottom: 3px; }
  .features li::before {
    content: ""; position: absolute; left: 0; top: 10px;
    width: 5px; height: 5px; border-radius: 50%; background: var(--ink);
  }
  .cert-row {
    position: absolute; left: 26px; bottom: 58px;
    display: flex; align-items: flex-end; gap: 6px;
  }
  .cert-badge {
    width: 52px; height: 52px; background: var(--ink); border-radius: 4px;
  }
  .social-tile {
    width: 24px; height: 30px; background: var(--ink); border-radius: 3px;
  }
  .cert-label {
    position: absolute; left: 26px; bottom: 44px;
    font-family: "Pragati Narrow", sans-serif; font-size: 10px;
    color: var(--ink); letter-spacing: 1px;
  }
  .web {
    position: absolute; left: 26px; bottom: 18px;
    font-family: "Pragati Narrow", sans-serif; font-weight: 700;
    font-size: 17px; color: var(--ink);
  }

  /* story side */
  .story {
    position: absolute; top: 270px; left: 24px; right: 24px;
    text-align: center; color: var(--ink);
    font-family: "Kalam", cursive; font-weight: 300;
  }
  .story__heading {
    font-family: "Pragati Narrow", sans-serif; font-size: 15px;
    letter-spacing: 0.5px; margin-bottom: 22px; text-transform: uppercase;
  }
  .story__text { font-size: 14px; line-height: 1.5; }
  .product-window {
    position: absolute; left: 22px; right: 22px; top: 630px; height: 200px;
    background: linear-gradient(160deg, #6e5a45 0%, #cbb9a0 40%, #e6d9c5 60%, #5d4a38 100%);
  }
</style>
</head>
<body>
  <div class="box-net">

    <section class="panel panel--side panel--features">
      <div class="band"></div>
      <ul class="features">
        <li>Compostable</li>
        <li>Vegan, gluten-free</li>
        <li>Plastic free, Non-toxic</li>
        <li>Biodegrades in less than 24 months</li>
        <li>Made from renewable resources</li>
        <li>Eco friendly and low environmental impact</li>
        <li>Does not get soggy or leave any residue in the drink</li>
        <li>Not made in China</li>
      </ul>
      <div class="cert-row">
        <div class="cert-badge" aria-label="KMB approved badge"></div>
        <div class="social-tile"></div>
        <div class="social-tile"></div>
        <div class="social-tile"></div>
      </div>
      <div class="cert-label">KMB APPROVED</div>
      <div class="web">www.pelvarix.com</div>
    </section>

    <section class="panel panel--front">
      <div class="band"></div>
      <svg class="tear-window" width="420" height="880" viewBox="0 0 420 880" aria-hidden="true">
        <polyline points="122,0 46,220 122,345" fill="none" stroke="#1c1a17" stroke-width="1.6" stroke-dasharray="6 5"/>
        <polyline points="286,0 370,220 290,345" fill="none" stroke="#1c1a17" stroke-width="1.6" stroke-dasharray="6 5"/>
        <line x1="122" y1="345" x2="290" y2="345" stroke="#1c1a17" stroke-width="1.6" stroke-dasharray="3 3"/>
      </svg>
      <div class="brand">
        <div class="brand__name"><span class="brand__dot"></span>Pelvarix.com</div>
        <div class="brand__tagline">NATURAL 100% BIODEGRADABLE</div>
      </div>
      <h1 class="title">
        <div class="title__lead">biodegradable</div>
        <div class="title__main">straws</div>
      </h1>
      <div class="turtle-art" role="img" aria-label="Ornamental teal sea turtle illustration"></div>
      <div class="count">200 straws</div>
    </section>

    <section class="panel panel--side panel--story">
      <div class="band"></div>
      <div class="story">
        <h2 class="story__heading">Sustainably Green</h2>
        <p class="story__text">Eco-friendly and low environmental impact do not always come together so seamlessly in one product. These plant-based straws will aid in reducing the ecological footprint on the South American ecosystem. We use what would have been tossed. We recycle the by-products of agricultural practices and manufacture a new product. Plant fibers lend us a renewable resource that future generations can appreciate. The process is clean, simple, and unobtrusive to the communities we are a part of.</p>
      </div>
      <div class="product-window" role="img" aria-label="Photo of natural fiber straws on a wooden table"></div>
    </section>

  </div>
</body>
</html>
```